TEBSIRK HOA Portal Site for Public

Clean up and organize current website; need website to look good and functional; this is a HOA (homeowner association management) website where homeowners can login and pay their bill, general information about a HOA, monthly newsletter page.
Competitors:
https://quillmarsh.example/
https://dorvinpalms.example/
https://www.kelbrookhomes.example/nevada
http://www.tpw-hoa.example/

Target Market(s)

homeowners

Industry/Entity Type

Real Estate

Coding

Coded - Design and coding required

Number of Pages Required

5+ page

Font styles to use
Serif

Colors
0292cd
33a6d7
e667a6
e34297

Requirements
Must have
• login to pay
• services page
• contact us
• order resale package
Nice to have
• page why an HOA would contract us

```html
<!DOCTYPE html>
<html lang="en">
<head>
<meta charset="utf-8">
<title>TEBSIRK HOA – Homeowner Association Management</title>
<link href="https://fonts.googleapis.com/css2?family=Lato:wght@400;700;900&display=swap" rel="stylesheet">
<style>
:root{
  --blue:#0292cd;
  --blue-light:#33a6d7;
  --pink:#e34297;
  --pink-light:#e667a6;
  --ink:#222;
  --body:#555;
  --grey-bg:#f1f1f1;
  --footer-bg:#1c1c1c;
  --white:#fff;
}
*{box-sizing:border-box;margin:0;padding:0}
html,body{width:1200px;height:3849px;overflow:hidden}
body{font-family:'Lato',sans-serif;color:var(--body);background:var(--white);position:relative}
.abs{position:absolute}
.center{left:0;width:1200px;text-align:center}
.btn{position:absolute;display:flex;align-items:center;justify-content:center;color:var(--white);font-weight:700;border-radius:3px}
.btn-blue{background:var(--blue)}
.btn-pink{background:var(--pink)}
.section-title{position:absolute;left:0;width:1200px;text-align:center;color:var(--pink);font-weight:700;font-size:38px}
.title-rule{position:absolute;left:555px;width:90px;height:3px;background:var(--blue)}
.copy{font-size:11.5px;line-height:20px;color:var(--body)}

/* top bar */
.topbar{top:0;left:0;width:1200px;height:45px;background:var(--blue);color:var(--white);font-size:12px}
.topbar .mail{position:absolute;left:162px;top:15px;display:flex;align-items:center;gap:6px}
.topbar .phone{position:absolute;right:162px;top:15px;display:flex;align-items:center;gap:10px}

/* nav */
.nav{top:45px;left:0;width:1200px;height:60px;background:var(--white)}
.brand{position:absolute;left:162px;top:17px;color:var(--pink);font-weight:700;font-size:22px}
.menu{position:absolute;left:630px;top:22px;display:flex;gap:24px;font-size:12px;color:#444}
.menu .active{color:var(--blue);position:relative}
.menu .active::before{content:"";position:absolute;left:50%;top:-17px;width:1px;height:11px;background:var(--blue)}
.menu .active::after{content:"";position:absolute;left:calc(50% - 3px);top:-8px;width:6px;height:6px;border-radius:50%;background:var(--blue)}
.search{position:absolute;left:1008px;top:16px;width:30px;height:30px;border-radius:50%;background:#eee;display:flex;align-items:center;justify-content:center}

/* hero */
.hero{top:105px;left:0;width:1200px;height:600px;background:linear-gradient(180deg,#3a2630 0%,#4a3430 45%,#3a2e24 100%)}
.hero .kicker{top:158px;font-size:19px;font-weight:700;color:var(--white)}
.hero h1{top:192px;font-size:45px;line-height:46px;color:var(--pink);font-weight:700}
.hero p{top:296px;font-size:13px;line-height:21px;color:#eee}

/* about */
.about{top:705px;left:0;width:1200px;height:390px;background:var(--grey-bg)}

/* services */
.service-num{position:absolute;font-size:34px;font-weight:700;color:#ccc}
.service-head{position:absolute;font-size:23px;font-weight:700;color:var(--ink)}
.service-copy{position:absolute;width:430px}
.accent-box{position:absolute;background:var(--blue);border-radius:12px}
.photo{position:absolute}

/* why */
.why{top:2029px;left:0;width:1200px;height:391px;background:linear-gradient(120deg,#2e2f31 0%,#3d3b3a 55%,#2a2a2c 100%)}
.why .copy{color:#e8e8e8}

/* order band */
.order{top:2420px;left:0;width:1200px;height:90px;background:var(--blue)}
.order h2{position:absolute;left:162px;top:24px;font-size:34px;color:var(--white);font-weight:700}

/* testimonials */
.card{position:absolute;top:2674px;width:278px;height:153px;background:var(--white);box-shadow:0 0 8px rgba(0,0,0,.15);padding:20px 13px;font-size:11.5px;line-height:19.5px}
.card::after{content:"";position:absolute;left:30px;bottom:-10px;border-left:10px solid transparent;border-right:10px solid transparent;border-top:10px solid var(--white)}
.avatar{position:absolute;top:2854px;width:60px;height:60px;border-radius:50%;background:linear-gradient(160deg,#c9ced6,#5a6270)}
.client{position:absolute;top:2877px;font-size:12px;font-weight:700;color:var(--blue)}

/* contact */
.field{position:absolute;background:var(--white);box-shadow:0 0 6px rgba(0,0,0,.14);font-size:12px;color:#666;padding:16px 13px}

/* newsletter */
.newsletter{top:3406px;left:0;width:1200px;height:97px;background:var(--pink)}
.newsletter h2{position:absolute;left:162px;top:22px;font-size:30px;color:var(--white);font-weight:700}
.newsletter p{position:absolute;left:164px;top:60px;font-size:11px;color:#fbd3e7}

/* footer */
.footer{top:3503px;left:0;width:1200px;height:301px;background:var(--footer-bg);color:#ddd}
.footer h4{position:absolute;top:42px;font-size:15px;color:var(--white);font-weight:700}
.footer h4::after{content:"";position:absolute;left:0;top:26px;width:38px;height:2px;background:var(--blue)}
.footer .brand-foot{position:absolute;left:162px;top:40px;color:var(--pink);font-weight:700;font-size:22px}
.footer .about-foot{position:absolute;left:162px;top:94px;width:210px;font-size:11.5px;line-height:19.5px}
.links{position:absolute;top:94px;list-style:none;font-size:11.5px;line-height:24px}
.links li{padding-left:16px;position:relative}
.links li::before{content:"";position:absolute;left:0;top:9px;width:6px;height:6px;border:1px solid var(--blue);border-radius:50%}
.social{position:absolute;left:160px;top:3703px;display:flex;gap:8px}
.social span{width:38px;height:38px;border-radius:50%;border:1.5px solid var(--white)}
.social span.on{background:var(--blue);border-color:var(--blue)}
.info-row{position:absolute;left:837px;display:flex;gap:16px;font-size:11.5px;line-height:17px;color:var(--white)}
.copyright{top:3804px;left:0;width:1200px;height:45px;background:var(--blue);color:var(--white);font-size:11.5px;display:flex;align-items:center;justify-content:center}
</style>
</head>
<body>

<header class="abs topbar">
  <div class="mail">
    <svg width="18" height="13" viewBox="0 0 18 13"><rect width="18" height="13" rx="3" fill="#e667a6"/><path d="M2 3l7 5 7-5" stroke="#fff" stroke-width="1.4" fill="none"/></svg>
    info@tebsirkhoa.example
  </div>
  <div class="phone">
    <svg width="20" height="20" viewBox="0 0 20 20"><path d="M5 2l3 4-2 2c1 2 3 4 5 5l2-2 4 3-2 3C9 17 3 11 2 4z" fill="#e667a6"/></svg>
    +91-000-000-0000
  </div>
</header>

<nav class="abs nav">
  <div class="brand">TEBSIRK HOA</div>
  <div class="menu">
    <span>Home</span><span class="active">About Us</span><span>Services</span><span>Why Us</span><span>Contact Us</span>
  </div>
  <div class="search"><svg width="13" height="13" viewBox="0 0 13 13"><circle cx="5.5" cy="5.5" r="4" stroke="#222" stroke-width="1.8" fill="none"/><path d="M8.5 8.5l3.5 3.5" stroke="#222" stroke-width="1.8"/></svg></div>
</nav>

<section class="abs hero" role="img" aria-label="Suburban family house at dusk">
  <div class="abs center kicker">TEBSIRK HOA</div>
  <h1 class="abs center">Homeowner Association<br>Management</h1>
  <p class="abs center">Lorem Ipsum is simply dummy text of the printing and typesetting industry. Lorem<br>Ipsum has been the industry's standard dummy text ever since the 1500s</p>
  <div class="btn btn-pink" style="left:457px;top:372px;width:134px;height:44px;font-size:18px">Login Now</div>
  <div class="btn btn-blue" style="left:608px;top:372px;width:134px;height:44px;font-size:18px">Contact Us</div>
</section>

<section class="abs about">
  <h2 class="section-title" style="top:44px">About Us</h2>
  <p class="abs center copy" style="top:128px">Lorem Ipsum is simply dummy text of the printing and typesetting industry. Lorem Ipsum has been the industry's<br>standard dummy text ever since the 1500s, when an unknown printer took a galley of type and scrambled it to<br>make a type specimen book.</p>
  <p class="abs center copy" style="top:206px">It has survived not only five centuries, but also the leap into electronic typesetting, remaining essentially<br>unchanged.</p>
  <div class="btn btn-blue" style="left:544px;top:281px;width:112px;height:36px;font-size:14px">Get Started</div>
</section>

<h2 class="section-title" style="top:1145px">Services We Provide</h2>
<div class="title-rule" style="top:1195px"></div>

<div class="accent-box" style="left:1001px;top:1227px;width:220px;height:337px"></div>
<div class="photo" role="img" aria-label="Two-storey suburban house at sunset" style="left:678px;top:1264px;width:487px;height:261px;background:linear-gradient(180deg,#9aa6d6 0%,#d9a8c4 45%,#3b4664 70%,#5d6b5a 100%)"></div>
<div class="service-num" style="left:162px;top:1232px">1.</div>
<div class="service-head" style="left:162px;top:1280px">Home owner Association Services</div>
<div class="service-copy copy" style="left:162px;top:1331px">Lorem Ipsum is simply dummy text of the printing and typesetting industry. Lorem Ipsum has been the industry's standard dummy text ever since the 1500s, when an unknown printer took a galley of type and scrambled it to make a type specimen book.<br><br>It has survived not only five centuries, but also the leap into electronic typesetting, remaining essentially unchanged.</div>
<div class="btn btn-pink" style="left:162px;top:1509px;width:111px;height:36px;font-size:14px">Know More</div>

<div class="accent-box" style="left:-20px;top:1617px;width:214px;height:336px"></div>
<div class="photo" role="img" aria-label="Grey split-level house for sale" style="left:30px;top:1654px;width:487px;height:261px;background:linear-gradient(180deg,#6f8a5c 0%,#8d929a 35%,#9a9ea4 70%,#6a7a4c 100%)"></div>
<div class="service-num" style="left:613px;top:1622px">2.</div>
<div class="service-head" style="left:613px;top:1670px">Home owner Association Services</div>
<div class="service-copy copy" style="left:613px;top:1721px">Lorem Ipsum is simply dummy text of the printing and typesetting industry. Lorem Ipsum has been the industry's standard dummy text ever since the 1500s, when an unknown printer took a galley of type and scrambled it to make a type specimen book.<br><br>It has survived not only five centuries, but also the leap into electronic typesetting, remaining essentially unchanged.</div>
<div class="btn btn-pink" style="left:611px;top:1898px;width:112px;height:37px;font-size:14px">Know More</div>

<section class="abs why" role="img" aria-label="Hand holding house keys">
  <h2 class="section-title" style="top:42px">Why an HOA would Contract Us</h2>
  <div class="title-rule" style="top:92px"></div>
  <p class="abs center copy" style="top:127px">Lorem Ipsum is simply dummy text of the printing and typesetting industry. Lorem Ipsum has been the industry's<br>standard dummy text ever since the 1500s, when an unknown printer took a galley of type and scrambled it to<br>make a type specimen book.</p>
  <p class="abs center copy" style="top:205px">It has survived not only five centuries, but also the leap into electronic typesetting, remaining essentially<br>unchanged.</p>
  <div class="btn btn-blue" style="left:544px;top:282px;width:112px;height:36px;font-size:14px">Learn More</div>
</section>

<section class="abs order">
  <h2>Order Resale Package Now</h2>
  <div class="btn btn-pink" style="left:926px;top:26px;width:112px;height:34px;font-size:14px;border:1px solid #fff">Login Now</div>
</section>

<h2 class="section-title" style="top:2578px">What Our Clients Say</h2>

<div class="card" style="left:162px">Lorem Ipsum is simply dummy text of the printing and typesetting industry. Lorem Ipsum has been the industry's standard dummy text ever since the 1500s, when an unknown printer took a galley of type and scrambled it to make a type specimen book.</div>
<div class="card" style="left:461px">Lorem Ipsum is simply dummy text of the printing and typesetting industry. Lorem Ipsum has been the industry's standard dummy text ever since the 1500s, when an unknown printer took a galley of type and scrambled it to make a type specimen book.</div>
<div class="card" style="left:761px">Lorem Ipsum is simply dummy text of the printing and typesetting industry. Lorem Ipsum has been the industry's standard dummy text ever since the 1500s, when an unknown printer took a galley of type and scrambled it to make a type specimen book.</div>
<div class="avatar" role="img" aria-label="Client portrait" style="left:180px"></div>
<div class="client" style="left:248px">-Client Name</div>
<div class="avatar" role="img" aria-label="Client portrait" style="left:479px"></div>
<div class="client" style="left:548px">-Client Name</div>
<div class="avatar" role="img" aria-label="Client portrait" style="left:779px"></div>
<div class="client" style="left:848px">-Client Name</div>

<div class="abs" style="top:2955px;left:0;width:1200px;height:1px;background:#e4e4e4"></div>

<h2 class="section-title" style="top:2990px">Contact Us</h2>
<div class="field" style="left:162px;top:3090px;width:280px;height:45px">Name:</div>
<div class="field" style="left:460px;top:3090px;width:280px;height:45px">Email:</div>
<div class="field" style="left:758px;top:3090px;width:280px;height:45px">Phone:</div>
<div class="field" style="left:162px;top:3157px;width:876px;height:93px">Message:</div>
<div class="btn btn-blue" style="left:544px;top:3297px;width:112px;height:36px;font-size:14px">Submit</div>

<section class="abs newsletter">
  <h2>Subcribe Now for Our Newsletter</h2>
  <p>Stay current with our news and insight &amp; updates</p>
  <div class="btn btn-blue" style="left:904px;top:27px;width:134px;height:37px;font-size:14px">Subscribe Now!</div>
</section>

<footer class="abs footer">
  <div class="brand-foot">TEBSIRK HOA</div>
  <p class="about-foot">Lorem Ipsum is simply dummy text of the printing and typesetting industry. Lorem Ipsum has been the industry's standard dummy text ever since .</p>

  <h4 style="left:386px">Quick Links</h4>
  <ul class="links" style="left:386px"><li>Home</li><li>About us</li><li>Services</li><li>Why Us?</li><li>Contact Us</li></ul>

  <h4 style="left:613px">Sitemap</h4>
  <ul class="links" style="left:613px;line-height:22.5px"><li>Home Owner</li><li>Terms &amp; Conditions</li><li>Support</li><li>Policy</li><li>FAQ</li></ul>

  <h4 style="left:837px">Contact Info</h4>
</footer>

<div class="social" aria-label="Social profiles"><span></span><span></span><span class="on"></span><span></span></div>

<div class="info-row" style="top:3630px;align-items:center">
  <svg width="22" height="22" viewBox="0 0 20 20"><path d="M5 2l3 4-2 2c1 2 3 4 5 5l2-2 4 3-2 3C9 17 3 11 2 4z" fill="none" stroke="#0292cd" stroke-width="1.6"/></svg>
  <span>+91-000-000-0000</span>
</div>
<div class="info-row" style="top:3670px">
  <svg width="22" height="26" viewBox="0 0 22 26"><path d="M11 1a8 8 0 0 0-8 8c0 6 8 16 8 16s8-10 8-16a8 8 0 0 0-8-8z" fill="#0292cd"/><circle cx="11" cy="9" r="3" fill="#1c1c1c"/></svg>
  <span>100- lorem ipsum is simply<br>summy text.</span>
</div>
<div class="info-row" style="top:3728px;align-items:center">
  <svg width="22" height="16" viewBox="0 0 22 16"><rect width="22" height="16" fill="#0292cd"/><path d="M1 1l10 8 10-8" stroke="#1c1c1c" stroke-width="1.6" fill="none"/></svg>
  <span>info@tebsirkhoa.example</span>
</div>

<div class="abs copyright">© 2019, TEBSIRK HOA , All Rights Reserved.</div>

</body>
</html>
```